New Business Card Design

We would like to refresh our business cards and make them look better. We are an IT company specialising in Cloud Services, IT Managed Services, software and hardware. I have attached a PSD of our current design. Also attached our logo.
Updates

I have uploaded all new logos in EPS format.

Can you please edit all designs to include a job title for Marcus Hollis, eg. General Manager

Industry/Entity Type

Software

Colors
ffffff

Requirements
Must have
• Please use white background.
Should not have
• Black background

```html
<!DOCTYPE html>
<html lang="en">
<head>
<meta charset="utf-8">
<title>Meridian Systems – Business Cards</title>
<link href="https://fonts.googleapis.com/css2?family=Jost:wght@400;600&family=Open+Sans:wght@400;600&display=swap" rel="stylesheet">
<style>
  :root {
    --page-bg: #f3f3f1;
    --card-light: #f4f4f5;
    --card-mid: #e2e3e5;
    --steel: #8e949d;
    --accent-red: #c8352a;
    --ink: #2b2b2d;
    --ink-soft: #4a4a4e;
    --white: #ffffff;
  }
  * { margin: 0; padding: 0; box-sizing: border-box; }
  html, body { width: 1200px; height: 720px; overflow: hidden; }
  body {
    background: var(--page-bg);
    display: flex;
    align-items: center;
    justify-content: center;
    gap: 30px;
    font-family: "Jost", sans-serif;
  }
  .card {
    position: relative;
    width: 555px;
    height: 317px;
    overflow: hidden;
    background: linear-gradient(160deg, var(--card-light) 0%, var(--card-mid) 55%, var(--card-light) 100%);
    box-shadow: 0 2px 10px rgba(0, 0, 0, 0.12);
  }
  .card-swoosh { position: absolute; inset: 0; width: 100%; height: 100%; }

  .brand { display: flex; align-items: center; gap: 12px; white-space: nowrap; }
  .brand-dot {
    flex: none;
    width: 42px; height: 42px; border-radius: 50%;
    background: var(--accent-red);
  }
  .brand-name {
    font-family: "Jost", sans-serif;
    font-weight: 400;
    font-size: 30px;
    line-height: 1;
    letter-spacing: 3px;
    color: var(--ink);
    text-transform: lowercase;
    white-space: nowrap;
  }

  /* Front */
  .card-front .brand { position: absolute; left: 60px; top: 40px; }
  .contact-list {
    position: absolute; left: 90px; top: 124px;
    list-style: none;
    font-family: "Open Sans", sans-serif;
    font-size: 12.5px;
    color: var(--ink-soft);
  }
  .contact-list li { display: flex; align-items: center; gap: 8px; height: 20px; }
  .contact-icon {
    width: 12px; height: 12px; border-radius: 50%;
    background: var(--accent-red);
    display: inline-flex; align-items: center; justify-content: center;
  }
  .contact-icon svg { width: 8px; height: 8px; }
  .holder {
    position: absolute; right: 22px; top: 108px;
    text-align: right; color: var(--white);
    font-family: "Open Sans", sans-serif;
    white-space: nowrap;
  }
  .holder-name { font-weight: 600; font-size: 17px; }
  .holder-title { font-size: 12.5px; margin-top: 2px; }

  /* Back */
  .card-back .brand { position: absolute; left: 50%; top: 96px; transform: translateX(-50%); }
  .back-domain {
    position: absolute; left: 0; right: 0; top: 150px;
    text-align: center;
    font-size: 15px; letter-spacing: 2px; color: var(--ink-soft);
    padding-left: 140px;
    white-space: nowrap;
  }
  .back-web {
    position: absolute; left: 0; right: 0; bottom: 62px;
    text-align: center;
    font-size: 19px; letter-spacing: 4px; color: var(--ink);
    white-space: nowrap;
  }
</style>
</head>
<body>

  <section class="card card-front">
    <svg class="card-swoosh" viewBox="0 0 555 317" preserveAspectRatio="none" aria-hidden="true">
      <path d="M0 262 C150 270 270 245 345 170 C395 120 425 40 485 0 L555 0 L555 317 L0 317 Z" fill="var(--steel)"/>
      <path d="M0 262 C150 270 270 245 345 170 C395 120 425 40 485 0" fill="none" stroke="var(--accent-red)" stroke-width="5"/>
      <path d="M0 271 C150 279 275 254 352 178 C402 128 432 48 497 0" fill="none" stroke="var(--white)" stroke-width="3"/>
      <path d="M0 287 C150 299 330 291 555 226 L555 317 L0 317 Z" fill="var(--card-light)"/>
      <path d="M0 293 C150 304 330 296 555 233" fill="none" stroke="var(--accent-red)" stroke-width="5"/>
    </svg>

    <div class="brand">
      <span class="brand-dot"></span>
      <span class="brand-name">Meridian Systems</span>
    </div>

    <ul class="contact-list">
      <li>
        <span class="contact-icon"><svg viewBox="0 0 8 8"><path d="M2 1 L3 3 L2.5 3.8 Q3.5 5 4.2 5.5 L5 5 L7 6 L6.4 7.2 Q3 7 0.8 1.6 Z" fill="var(--white)"/></svg></span>
        07 3180 4455
      </li>
      <li>
        <span class="contact-icon"><svg viewBox="0 0 8 8"><rect x="2.5" y="1" width="3" height="6" rx="0.6" fill="var(--white)"/></svg></span>
        0491 552 607
      </li>
      <li>
        <span class="contact-icon"><svg viewBox="0 0 8 8"><rect x="1.2" y="2.2" width="5.6" height="3.8" fill="var(--white)"/><path d="M1.2 2.2 L4 4.4 L6.8 2.2" fill="none" stroke="var(--accent-red)" stroke-width="0.6"/></svg></span>
        hollism@meridianit.com.au
      </li>
      <li>
        <span class="contact-icon"><svg viewBox="0 0 8 8"><circle cx="4" cy="4" r="2.6" fill="none" stroke="var(--white)" stroke-width="0.8"/><path d="M1.4 4 H6.6 M4 1.4 V6.6" stroke="var(--white)" stroke-width="0.6"/></svg></span>
        www.meridianit.com.au
      </li>
    </ul>

    <div class="holder">
      <p class="holder-name">Marcus Hollis</p>
      <p class="holder-title">General Manager</p>
    </div>
  </section>

  <section class="card card-back">
    <div class="brand">
      <span class="brand-dot"></span>
      <span class="brand-name">Meridian Systems</span>
    </div>
    <p class="back-domain">meridianit.com.au</p>
    <p class="back-web">www.meridianit.com.au</p>
  </section>

</body>
</html>
```